Federal Government Proposal Development Consulting company needs a website designed and coded

I am looking for someone to design (using an existing logo, color palette, and text fonts) and code a wordpress-based website for a Proposal Development consulting company. I have full copy for all site pages and suggestions for images/ graphics and a few example design templates to go from.

One note, from a color perspective - I included a mockup of a business card to highlight a color scheme that I tend to like - if you look at the back of the business card, the blend of the grey, blue, with the neon green highlight as a separator really seems to pop. Just a thought as you are designing the page.

I would like to see 2-3 potential design layouts, and I will select one to move forward with. Then, I would like the site to be coded for WordPress (I can provide a login to my wordpress site). I would like 1 opportunity to review the coded site and make any final tweaks.

```html
<!DOCTYPE html>
<html lang="en">
<head>
<meta charset="utf-8">
<title>The Bright Quill – Proposal Consulting</title>
<link rel="stylesheet" href="https://fonts.googleapis.com/css2?family=Bebas+Neue&family=Fondamento&family=Montserrat:wght@400;500;600;700&display=swap">
<style>
:root{
  --navy:#0d1463;
  --blue:#0a45c8;
  --blue-dark:#0733a6;
  --ink:#222431;
  --text:#4a4c58;
  --grey-bg:#f4f4f5;
  --line:#d9dbe3;
  --footer:#07084a;
  --star:#f2b51d;
  --white:#ffffff;
}
*{box-sizing:border-box;margin:0;padding:0}
html,body{width:1200px;height:4930px;overflow:hidden}
body{font-family:"Montserrat",Arial,sans-serif;color:var(--text);background:var(--white);position:relative}
section,header,footer{position:absolute;left:0;width:1200px}
.script{font-family:"Fondamento",Georgia,serif;color:var(--navy);font-weight:400}
.btn{display:inline-flex;align-items:center;justify-content:center;background:var(--blue);color:var(--white);font-size:11px;text-transform:uppercase;border-radius:20px;letter-spacing:.3px;position:absolute}

/* header */
.site-header{top:0;height:76px;background:var(--white);box-shadow:0 2px 8px rgba(0,0,0,.06);z-index:2}
.brand{position:absolute;left:140px;top:18px;display:flex;align-items:center;gap:10px}
.brand-name{font-family:"Fondamento",Georgia,serif;font-size:21px;color:var(--navy)}
.brand-dot{width:14px;height:14px;border-radius:50%;background:var(--navy)}
.main-nav{position:absolute;top:29px;left:562px;display:flex;gap:34px;font-size:11.5px;color:var(--ink);text-transform:uppercase}
.nav-contact{left:968px;top:22px;width:90px;height:32px}

/* hero */
.hero{top:76px;height:530px}
.hero-visual{position:absolute;inset:0;background:linear-gradient(100deg,#1b2333 0%,#2a3446 38%,#3a4f6c 60%,#6d8fb3 78%,#2a3d5a 100%)}
.hero-glow{position:absolute;left:720px;top:110px;width:300px;height:300px;border-radius:50%;background:radial-gradient(circle,rgba(255,190,120,.55) 0%,rgba(120,170,230,.25) 45%,rgba(0,0,0,0) 70%)}
.hero-kicker{position:absolute;left:143px;top:124px;font-family:"Fondamento",Georgia,serif;font-size:36px;color:var(--white)}
.hero-title{position:absolute;left:143px;top:170px;font-family:"Bebas Neue",Impact,sans-serif;font-size:56px;line-height:54px;color:var(--white);letter-spacing:.5px}
.hero-cta{position:absolute;left:143px;top:362px;width:330px;height:38px;border:1.5px solid var(--white);border-radius:20px;color:var(--white);font-size:11.5px;display:flex;align-items:center;padding-left:32px;gap:14px;text-transform:uppercase}

/* what we do */
.what{top:606px;height:891px}
.section-title{position:absolute;left:0;width:100%;text-align:center;font-size:36px}
.what .section-title{top:80px}
.what-intro{position:absolute;left:150px;width:900px;top:146px;text-align:center;font-size:11.6px;line-height:23px}
.what-intro p+p{margin-top:6px}
.what-intro b{color:var(--ink)}
.service-card{position:absolute;top:397px;width:282px;height:398px;background:var(--white);border-radius:8px;box-shadow:0 6px 20px rgba(0,0,0,.09);padding:56px 22px 0 24px}
.card-icon{position:absolute;left:14px;top:-42px;width:72px;height:72px;border-radius:50%;background:var(--blue);display:flex;align-items:center;justify-content:center;border:3px solid var(--white);box-shadow:0 2px 6px rgba(0,0,0,.15)}
.card-title{font-size:16px;margin-bottom:20px}
.card-body{font-size:10.3px;line-height:20px;letter-spacing:.2px}
.card-body p+p{margin-top:8px}

/* who we are */
.who{top:1497px;height:583px;background:var(--grey-bg)}
.who-visual{position:absolute;left:141px;top:81px;width:432px;height:418px;border-radius:10px;background:linear-gradient(160deg,#e9ecef 0%,#cfd5dc 45%,#7d858f 80%,#4b4f57 100%)}
.who .script{position:absolute;left:623px;top:88px;font-size:36px}
.who-text{position:absolute;left:623px;top:155px;width:436px;font-size:11.8px;line-height:23px}
.who-btn{left:623px;top:458px;width:141px;height:34px}

/* services */
.services{top:2080px;height:720px}
.services .section-title{top:78px}
.svc-grid{position:absolute;left:186px;top:148px;display:grid;grid-template-columns:repeat(5,154px);grid-auto-rows:124px;column-gap:14px;row-gap:18px}
.svc{background:var(--white);box-shadow:0 3px 12px rgba(0,0,0,.08);display:flex;flex-direction:column;align-items:center;justify-content:center;text-align:center;font-size:12.5px;line-height:15px;color:var(--ink);gap:8px}
.svc svg{width:46px;height:46px;color:var(--navy)}
.svc.is-active{background:var(--blue);color:var(--white);font-weight:600}
.svc.is-active svg{color:var(--white)}
.svc-btn{left:529px;top:605px;width:142px;height:33px}

/* expertise */
.expertise{top:2800px;height:665px;background:var(--grey-bg)}
.expertise .script{position:absolute;left:143px;top:84px;font-size:36px}
.sme-list{position:absolute;left:143px;top:158px;list-style:none}
.sme-list li{display:flex;align-items:center;gap:17px;height:35.7px;font-size:13px;color:var(--ink)}
.sme-visual{position:absolute;left:630px;top:93px;width:432px;height:483px;border-radius:12px;background:radial-gradient(circle at 48% 42%,#7fb4ff 0%,#1f5fb6 25%,#0c2d5e 60%,#06182f 100%)}

/* testimonials */
.testimonials{top:3465px;height:700px}
.testimonials .section-title{top:107px}
.t-card{position:absolute;width:288px;background:var(--white);box-shadow:0 4px 18px rgba(0,0,0,.09);padding:18px 20px;font-size:11.2px;line-height:21px;color:var(--ink)}
.t-head{display:flex;align-items:center;gap:18px;margin-bottom:10px}
.avatar{width:50px;height:50px;border-radius:50%;background:linear-gradient(135deg,#b5876a,#6b4a3a)}
.stars{display:flex;gap:4px}
.t-name{font-weight:700;font-size:13px;margin-bottom:2px}
.t-arrows{position:absolute;top:503px;left:514px;display:flex;gap:18px}
.arrow{width:56px;height:56px;border-radius:50%;display:flex;align-items:center;justify-content:center}
.arrow.prev{background:#5d6067}
.arrow.next{background:var(--blue)}

/* contact */
.contact{top:4165px;height:535px}
.contact-frame{position:absolute;left:148px;top:20px;width:904px;height:456px;background:var(--white);border-radius:10px;box-shadow:0 6px 24px rgba(0,0,0,.09)}
.contact-panel{position:absolute;left:170px;top:0;width:337px;height:430px;background:var(--blue);border-radius:10px;color:var(--white);padding:44px 36px}
.contact-panel .script{color:var(--white);font-size:34px}
.contact-lead{font-size:11.3px;line-height:20px;margin-top:18px}
.info{display:flex;gap:14px;margin-top:22px;font-size:11.5px;line-height:20px}
.info b{font-weight:600;display:block}
.socials{display:flex;gap:10px;margin-top:30px}
.socials span{width:26px;height:26px;border:1.5px solid var(--white);border-radius:50%}
.form{position:absolute;left:536px;top:0;width:490px}
.form .script{position:absolute;top:58px;font-size:34px;white-space:nowrap}
.field{position:absolute;width:232px;border-bottom:1px solid var(--line);padding-bottom:10px}
.field label{display:block;font-size:10px;color:#9a9ca6;margin-bottom:8px}
.field span{font-size:12px;color:var(--ink)}
.send{left:536px;top:390px;width:142px;height:34px}

/* footer */
.site-footer{top:4700px;height:230px;background:var(--footer);color:var(--white)}
.footer-brand{position:absolute;left:0;width:100%;top:46px;display:flex;justify-content:center;align-items:center;gap:10px}
.footer-brand .brand-name{color:var(--white)}
.footer-brand .brand-dot{background:var(--white)}
.footer-nav{position:absolute;top:143px;left:0;width:100%;display:flex;justify-content:center;gap:22px;font-size:11.5px;text-transform:uppercase}
.copy{position:absolute;top:198px;left:143px;font-size:11.5px}
.legal{position:absolute;top:198px;right:140px;font-size:11.5px;display:flex;gap:16px}
</style>
</head>
<body>
<svg width="0" height="0" style="position:absolute" aria-hidden="true">
  <defs>
    <symbol id="i-doc" viewBox="0 0 46 46"><g fill="none" stroke="currentColor" stroke-width="2"><rect x="10" y="5" width="26" height="36" rx="2"/><path d="M15 14h16M15 20h16M15 26h16M15 32h10"/></g></symbol>
    <symbol id="i-chip" viewBox="0 0 46 46"><g fill="none" stroke="currentColor" stroke-width="2"><rect x="13" y="13" width="20" height="20" rx="2"/><path d="M18 13V7M23 13V7M28 13V7M18 39v-6M23 39v-6M28 39v-6M13 18H7M13 23H7M13 28H7M39 18h-6M39 23h-6M39 28h-6"/></g><text x="23" y="27" font-size="9" font-family="Montserrat,sans-serif" text-anchor="middle" fill="currentColor">AI</text></symbol>
    <symbol id="i-bulb" viewBox="0 0 46 46"><g fill="none" stroke="currentColor" stroke-width="2"><circle cx="23" cy="17" r="8"/><path d="M20 25v4h6v-4M8 38l12-6h12M6 30l6 8"/></g></symbol>
    <symbol id="i-person" viewBox="0 0 46 46"><g fill="none" stroke="currentColor" stroke-width="2"><circle cx="23" cy="15" r="8"/><path d="M9 40c0-9 6-14 14-14s14 5 14 14"/></g></symbol>
    <symbol id="i-speaker" viewBox="0 0 46 46"><g fill="none" stroke="currentColor" stroke-width="2"><path d="M10 18h7l9-8v26l-9-8h-7z"/><path d="M31 16c3 4 3 10 0 14M35 12c5 6 5 16 0 22"/></g></symbol>
    <symbol id="i-book" viewBox="0 0 46 46"><g fill="none" stroke="currentColor" stroke-width="2"><rect x="8" y="8" width="30" height="30" rx="2"/><path d="M23 8v30M12 15h7M12 21h7M12 27h7M27 15h7M27 21h7M27 27h7"/></g></symbol>
    <symbol id="i-monitor" viewBox="0 0 46 46"><g fill="none" stroke="currentColor" stroke-width="2"><rect x="6" y="8" width="34" height="24" rx="2"/><path d="M18 38h10M23 32v6"/></g></symbol>
    <symbol id="i-pen" viewBox="0 0 46 46"><g fill="none" stroke="currentColor" stroke-width="2"><rect x="8" y="6" width="22" height="32" rx="2"/><path d="M13 14h12M13 20h12M13 26h6M38 12L24 34l-3 4 1-5 14-22z"/></g></symbol>
    <symbol id="tick" viewBox="0 0 18 18"><circle cx="9" cy="9" r="7.5" fill="none" stroke="#0a45c8" stroke-width="1.4"/><path d="M5.5 9.2l2.3 2.3 4.7-4.8" fill="none" stroke="#0a45c8" stroke-width="1.5"/></symbol>
    <symbol id="star" viewBox="0 0 20 20"><path d="M10 1l2.6 6 6.4.6-4.9 4.3 1.5 6.3L10 14.9 4.4 18.2l1.5-6.3L1 7.6 7.4 7z" fill="#f2b51d"/></symbol>
  </defs>
</svg>

<header class="site-header">
  <div class="brand"><span class="brand-name">The Bright Quill</span><span class="brand-dot"></span></div>
  <nav class="main-nav"><span>Home</span><span>Work With Us</span><span>Work For Us</span><span>About Us</span></nav>
  <span class="btn nav-contact">Contact</span>
</header>

<section class="hero">
  <div class="hero-visual" role="img" aria-label="Hands on a laptop with a glowing AI chip and technology icons overlay"><div class="hero-glow"></div></div>
  <div class="hero-kicker">Generate Success</div>
  <h1 class="hero-title">Fuel Innovation in<br>Proposal Excellence<br>with The Bright Quill!</h1>
  <div class="hero-cta">Click here to explore our services
    <svg width="18" height="18" viewBox="0 0 18 18"><circle cx="9" cy="9" r="8" fill="#fff"/><path d="M5.5 9.2l2.3 2.3 4.7-4.8" fill="none" stroke="#2a3446" stroke-width="1.6"/></svg>
  </div>
</section>

<section class="what">
  <h2 class="section-title script">What We Do</h2>
  <div class="what-intro">
    <p>The Bright Quill, specializes in advancing an organization through a comprehensive suite of services designed to modernize the proposal development process. From innovative Capture Management strategies that pinpoint lucrative opportunities, meticulous Proposal Development services that transform concepts into effective narratives, and cutting-edge Generative AI techniques that create domain-aware content accelerating proposal draft development, we are your dedicated partner in securing success. With a unique fusion of technical expertise and exceptional writing capabilities, we surpass industry standards and set new benchmarks for excellence.</p>
    <p>Discover a dynamic approach to proposal consulting that goes beyond conventional boundaries—choose The Bright Quill for solutions that <b>Enhance</b> the quality of your work, <b>Elevate</b> your corporate advantage, and <b>Expand</b> your industry presence.</p>
  </div>

  <article class="service-card" style="left:143px">
    <div class="card-icon"><svg width="40" height="40" style="color:#fff"><use href="#i-chip"/></svg></div>
    <h3 class="card-title script">Generative AI</h3>
    <div class="card-body">
      <p>Revolutionize your proposal writing process with our domain-aware Generative AI services. Using customer-installed tools, we leverage domain-aware artificial intelligence to generate innovative and tailored proposal content. This not only accelerates the proposal development timeline but also ensures content that is both dynamic and targeted.</p>
      <p>Stay ahead of the curve with proposals that not only meet industry standards but exceed expectations, thanks to the creative insights generated by our AI-driven approach.</p>
    </div>
  </article>
  <article class="service-card" style="left:459px">
    <div class="card-icon"><svg width="40" height="40" style="color:#fff"><use href="#i-person"/></svg></div>
    <h3 class="card-title script">Capture Management</h3>
    <div class="card-body">
      <p>Elevate your business development strategy with our Capture Management services. From opportunity identification to strategic planning, our experts will guide you through a meticulous process, ensuring the pursuit of the right contracts to position your organization for success.</p>
      <p>Trust us to analyze the market, mitigate risks, and develop strategies that maximize the ability to secure lucrative opportunities.</p>
    </div>
  </article>
  <article class="service-card" style="left:775px">
    <div class="card-icon"><svg width="40" height="40" style="color:#fff"><use href="#i-doc"/></svg></div>
    <h3 class="card-title script">Proposal Development</h3>
    <div class="card-body">
      <p>Transform your vision into winning proposals with our Proposal Development services. We specialize in persuasive narratives, clear technical solutions, and strategic pricing models. From meticulous compliance reviews to captivating executive summaries, we ensure every aspect of a proposal is polished &amp; aligned with your objectives.</p>
      <p>Turn your ideas into persuasive documents that leave a lasting impression on clients to set you apart from the competition.</p>
    </div>
  </article>
</section>

<section class="who">
  <div class="who-visual" role="img" aria-label="Two businessmen in a meeting at a table with a laptop"></div>
  <h2 class="script">Who We Are</h2>
  <div class="who-text">
    <p>It is a long established fact that a reader will be distracted by the readable content of a page when looking at its layout. The point of using Lorem Ipsum is that it has a more-or-less normal distribution of letters, as opposed to using 'Content here, content here', making it look like readable English. Many are desktop publishing packages and web page editors now use Lorem Ipsum as their default model text, and a search for 'lorem ipsum' will uncover many web sites still in their infancy.</p>
    <p>There are many variations of passages of Lorem Ipsum available, but the majority have suffered alteration in some form, by injected humour, or other randomised words which don't look even slightly believable.</p>
  </div>
  <span class="btn who-btn">About Us</span>
</section>

<section class="services">
  <h2 class="section-title script">Our Services</h2>
  <div class="svc-grid">
    <div class="svc is-active"><svg><use href="#i-chip"/></svg>Generative<br>AI</div>
    <div class="svc"><svg><use href="#i-bulb"/></svg>Technical<br>Solutioning</div>
    <div class="svc"><svg><use href="#i-person"/></svg>Competitive<br>Intelligence</div>
    <div class="svc"><svg><use href="#i-person"/></svg>Capture<br>Management</div>
    <div class="svc"><svg><use href="#i-doc"/></svg>Proposal<br>Management</div>
    <div class="svc"><svg><use href="#i-doc"/></svg>Compliance<br>Reviews</div>
    <div class="svc"><svg><use href="#i-person"/></svg>Executive<br>Summaries</div>
    <div class="svc"><svg><use href="#i-speaker"/></svg>Volume<br>Lead</div>
    <div class="svc"><svg><use href="#i-person"/></svg>Technical<br>Writer</div>
    <div class="svc"><svg><use href="#i-book"/></svg>Book<br>Boss</div>
    <div class="svc"><svg><use href="#i-pen"/></svg>Resume<br>Writer</div>
    <div class="svc"><svg><use href="#i-monitor"/></svg>Desktop<br>Publishing</div>
    <div class="svc"><svg><use href="#i-pen"/></svg>Proposal<br>Production</div>
    <div class="svc"><svg><use href="#i-doc"/></svg>Templates &amp;<br>Processes</div>
    <div class="svc"><svg><use href="#i-book"/></svg>Market<br>Survey</div>
  </div>
  <span class="btn svc-btn">Read More</span>
</section>

<section class="expertise">
  <h2 class="script">Subject Matter Expertise</h2>
  <ul class="sme-list">
    <li><svg width="18" height="18"><use href="#tick"/></svg>Generative AI</li>
    <li><svg width="18" height="18"><use href="#tick"/></svg>Software/ Hardware Engineering</li>
    <li><svg width="18" height="18"><use href="#tick"/></svg>Systems Engineering</li>
    <li><svg width="18" height="18"><use href="#tick"/></svg>High-Performance Computing (HPC)</li>
    <li><svg width="18" height="18"><use href="#tick"/></svg>Secure Supply Chain (ISO 28000 &amp; ISO 20243-1)</li>
    <li><svg width="18" height="18"><use href="#tick"/></svg>Logistics, Warehousing</li>
    <li><svg width="18" height="18"><use href="#tick"/></svg>Information Technology Support</li>
    <li><svg width="18" height="18"><use href="#tick"/></svg>Cybersecurity</li>
    <li><svg width="18" height="18"><use href="#tick"/></svg>Data Analysis</li>
    <li><svg width="18" height="18"><use href="#tick"/></svg>Systems Integration</li>
    <li><svg width="18" height="18"><use href="#tick"/></svg>Program Management</li>
    <li><svg width="18" height="18"><use href="#tick"/></svg>Systems Development &amp; Testing</li>
  </ul>
  <div class="sme-visual" role="img" aria-label="Hand holding a phone with glowing AI network icons"></div>
</section>

<section class="testimonials">
  <h2 class="section-title script">Client Testimonials</h2>

  <article class="t-card" style="left:-42px;top:245px;height:280px">
    <div class="t-head"><div class="avatar" role="img" aria-label="Client portrait"></div><div class="stars"><svg width="18" height="18"><use href="#star"/></svg><svg width="18" height="18"><use href="#star"/></svg><svg width="18" height="18"><use href="#star"/></svg><svg width="18" height="18"><use href="#star"/></svg><svg width="18" height="18"><use href="#star"/></svg></div></div>
    <div class="t-name">Marlow</div>
    <p>Lorem Ipsum is simply dummy text printing and typesetting industry Lorem Ipsum has been the industry' standard an unknown printer took a galley type and scrambled it to make a specimen book. It h survived not only centuries, but also the leap into electr typesetting,</p>
  </article>
  <article class="t-card" style="left:273px;top:175px;height:290px">
    <div class="t-head"><div class="avatar" role="img" aria-label="Client portrait"></div><div class="stars"><svg width="18" height="18"><use href="#star"/></svg><svg width="18" height="18"><use href="#star"/></svg><svg width="18" height="18"><use href="#star"/></svg><svg width="18" height="18"><use href="#star"/></svg><svg width="18" height="18"><use href="#star"/></svg></div></div>
    <div class="t-name">Daniel Hartley</div>
    <p>Lorem Ipsum is simply dummy text printing and typesetting industry Lorem Ipsum has been the industry' standard an unknown printer took a galley type and scrambled it to make a specimen book. It h survived not only centuries, but also the leap into electr typesetting,</p>
  </article>
  <article class="t-card" style="left:592px;top:175px;height:290px">
    <div class="t-head"><div class="avatar" role="img" aria-label="Client portrait" style="background:linear-gradient(135deg,#8a7060,#3c302a)"></div><div class="stars"><svg width="18" height="18"><use href="#star"/></svg><svg width="18" height="18"><use href="#star"/></svg><svg width="18" height="18"><use href="#star"/></svg><svg width="18" height="18"><use href="#star"/></svg><svg width="18" height="18"><use href="#star"/></svg></div></div>
    <div class="t-name">Grace Whitfield</div>
    <p>Lorem Ipsum is simply dummy text printing and typesetting industry Lorem Ipsum has been the industry' standard an unknown printer took a galley type and scrambled it to make a specimen book. It h survived not only centuries, but also the leap into electr typesetting,</p>
  </article>
  <article class="t-card" style="left:907px;top:245px;height:280px">
    <div class="t-head"><div class="avatar" role="img" aria-label="Client portrait"></div><div class="stars"><svg width="18" height="18"><use href="#star"/></svg><svg width="18" height="18"><use href="#star"/></svg><svg width="18" height="18"><use href="#star"/></svg><svg width="18" height="18"><use href="#star"/></svg><svg width="18" height="18"><use href="#star"/></svg></div></div>
    <div class="t-name">Oliver Pemberton</div>
    <p>Lorem Ipsum is simply dummy text printing and typesetting industry Lorem Ipsum has been the industry' standard an unknown printer took a galley type and scrambled it to make a specimen book. It h survived not only centuries, but also the leap into electr typesetting,</p>
  </article>

  <div class="t-arrows">
    <span class="arrow prev"><svg width="18" height="18" viewBox="0 0 18 18"><path d="M15 9H4M8 4L3 9l5 5" fill="none" stroke="#fff" stroke-width="1.8"/></svg></span>
    <span class="arrow next"><svg width="18" height="18" viewBox="0 0 18 18"><path d="M3 9h11M10 4l5 5-5 5" fill="none" stroke="#fff" stroke-width="1.8"/></svg></span>
  </div>
</section>

<section class="contact">
  <div class="contact-frame"></div>
  <div class="contact-panel">
    <h2 class="script">Contact Us</h2>
    <p class="contact-lead">Lorem Ipsum is simply dummy text of the printing and typesetting industry.</p>
    <div class="info"><svg width="16" height="20" viewBox="0 0 16 20"><path d="M8 1a6 6 0 0 0-6 6c0 5 6 12 6 12s6-7 6-12a6 6 0 0 0-6-6z" fill="#fff"/><circle cx="8" cy="7" r="2.2" fill="#0a45c8"/></svg><div><b>Address</b>48 Meridian Court, Suite 210,<br>Fairview, Texas</div></div>
    <div class="info"><svg width="16" height="16" viewBox="0 0 16 16"><path d="M3 1l3 3-1.5 2.5c1 2 3 4 5 5L12 10l3 3-2 2C7 15 1 9 1 3z" fill="#fff"/></svg><div><b>Phone</b>555 014 2290</div></div>
    <div class="info"><svg width="16" height="14" viewBox="0 0 16 14"><rect x="1" y="2" width="14" height="10" rx="1" fill="#fff"/><path d="M1 3l7 5 7-5" fill="none" stroke="#0a45c8" stroke-width="1.2"/></svg><div><b>Email</b>inquiry@brightquill.com</div></div>
    <div class="socials"><span></span><span></span><span></span><span></span></div>
  </div>
  <div class="form">
    <h2 class="script">Get In Touch</h2>
    <div class="field" style="left:0;top:130px"><label>Name</label><span>Lorem ipsum</span></div>
    <div class="field" style="left:256px;top:130px"><label>Email Address</label><span>info@brightquill.com</span></div>
    <div class="field" style="left:0;top:213px"><label>Company Name</label><span>Lorem ipsum</span></div>
    <div class="field" style="left:256px;top:213px"><label>Phone Number</label><span>555-014-2290</span></div>
    <div class="field" style="left:0;top:283px;width:488px;height:75px"><label>Message</label><span>Your Message is here</span></div>
  </div>
  <span class="btn send">Send Now</span>
</section>

<footer class="site-footer">
  <div class="footer-brand"><span class="brand-name">The Bright Quill</span><span class="brand-dot"></span></div>
  <nav class="footer-nav"><span>Home</span><span>|</span><span>Work With Us</span><span>|</span><span>Work For Us</span><span>|</span><span>About Us</span><span>|</span><span>Contact</span></nav>
  <div class="copy">© 2024 The Bright Quill. All Rights Reserved.</div>
  <div class="legal"><span>Privacy Policy</span><span>|</span><span>Terms &amp; Conditions</span></div>
</footer>
</body>
</html>
```